Dovecote Realty

Business cards for 4 people

They need to say for all
87 Tarrow Quay, Boston MA 02114

Each person will have their own personal information
We would like gold embossing for the name of the company
Marla is the blonde sitting in the chair smiling her information should be on the back of the card with her name and information
Should say for slogan classic pattern, elevated experience
marla@dovecoteprops.com
(413) 555-0182

Odette is the brunette with wavy hair in the tan suit celina@dovecoteprops.com
(617) 555-0137

faith@dovecoteprops.com
(413) 555-0164
standing next to the chair

hope@dovecoteprops.com
(413) 555-0199
close up headshot

```html
<!DOCTYPE html>
<html lang="en">
<head>
<meta charset="utf-8">
<title>Dovecote Realty – Business Card</title>
<link rel="stylesheet" href="https://fonts.googleapis.com/css2?family=Montserrat:wght@500;700&display=swap">
<style>
  :root {
    --navy: #1f2d4b;
    --navy-soft: #64748d;
    --gold: #d9a85f;
    --paper: #f1f1f1;
    --stage: #d9d9d9;
    --ink-grey: #3d4558;
  }
  * { box-sizing: border-box; margin: 0; padding: 0; }
  html, body { width: 1200px; height: 1200px; overflow: hidden; }
  body {
    background: var(--stage);
    font-family: "Montserrat", sans-serif;
    display: flex;
    flex-direction: column;
    align-items: center;
    justify-content: center;
    gap: 60px;
  }
  .card {
    position: relative;
    width: 840px;
    height: 480px;
    border-radius: 28px;
    overflow: hidden;
  }

  /* Front */
  .card-front {
    background: linear-gradient(120deg, var(--navy-soft) 0%, #42526f 35%, var(--navy) 70%);
    display: flex;
    flex-direction: column;
    align-items: center;
    justify-content: center;
    gap: 30px;
  }
  .brand-circle {
    width: 130px;
    height: 130px;
    border-radius: 50%;
    border: 4px solid var(--gold);
  }
  .brand-name {
    font-weight: 500;
    font-size: 46px;
    letter-spacing: 6px;
    text-transform: uppercase;
    color: var(--gold);
  }

  /* Back */
  .card-back { background: var(--paper); }
  .card-back .waves { position: absolute; inset: 0; }
  .person {
    position: absolute;
    left: 70px;
    top: 62px;
  }
  .person-name {
    font-weight: 700;
    font-size: 38px;
    color: var(--gold);
  }
  .person-title {
    margin-top: 4px;
    font-weight: 500;
    font-size: 19px;
    color: var(--ink-grey);
  }
  .back-brand {
    position: absolute;
    right: 60px;
    top: 50px;
    display: flex;
    flex-direction: column;
    align-items: center;
    gap: 16px;
  }
  .back-brand .brand-circle {
    width: 92px;
    height: 92px;
    border: 3px solid var(--navy);
  }
  .back-brand .brand-name {
    font-size: 26px;
    letter-spacing: 3px;
    color: var(--navy);
  }
  .contact {
    position: absolute;
    left: 80px;
    top: 314px;
    color: #ffffff;
    font-weight: 500;
    font-size: 18px;
    line-height: 1.35;
  }
  .address { margin-bottom: 12px; }
  .contact-list { list-style: none; }
  .contact-list li { display: flex; align-items: center; gap: 12px; }
  .contact-list svg { width: 16px; height: 16px; flex: none; fill: var(--gold); }
</style>
</head>
<body>

  <section class="card card-front" aria-label="Card front">
    <div class="brand-circle"></div>
    <div class="brand-name">Dovecote Realty</div>
  </section>

  <section class="card card-back" aria-label="Card back">
    <svg class="waves" viewBox="0 0 840 480" preserveAspectRatio="none" aria-hidden="true">
      <defs>
        <linearGradient id="navyFade" x1="0" y1="0" x2="1" y2="0">
          <stop offset="0" stop-color="#56647e"/>
          <stop offset="0.55" stop-color="#1f2d4b"/>
        </linearGradient>
      </defs>
      <path d="M0,300 C150,268 330,262 470,330 C560,372 620,420 655,480 L0,480 Z" fill="url(#navyFade)"/>
      <path d="M215,256 C420,234 620,300 722,480 L662,480 C592,362 440,276 215,256 Z" fill="#d9a85f"/>
      <path d="M840,195 C800,290 720,332 615,326 C680,370 730,420 762,480 L840,480 Z" fill="#1f2d4b"/>
    </svg>

    <div class="person">
      <div class="person-name">Marla Ashby</div>
      <div class="person-title">Founder &amp; Director</div>
    </div>

    <div class="back-brand">
      <div class="brand-circle"></div>
      <div class="brand-name">Dovecote Realty</div>
    </div>

    <div class="contact">
      <p class="address">87 Tarrow Quay, Boston,<br>MA 02114, United States</p>
      <ul class="contact-list">
        <li>
          <svg viewBox="0 0 24 24"><path d="M6.6 10.8a15.1 15.1 0 0 0 6.6 6.6l2.2-2.2a1 1 0 0 1 1-.25 11.4 11.4 0 0 0 3.6.57 1 1 0 0 1 1 1V20a1 1 0 0 1-1 1A17 17 0 0 1 3 4a1 1 0 0 1 1-1h3.5a1 1 0 0 1 1 1c0 1.25.2 2.45.57 3.57a1 1 0 0 1-.25 1z"/></svg>
          <span>(413) 555-0182</span>
        </li>
        <li>
          <svg viewBox="0 0 24 24"><path d="M2 5h20v14H2z M2 5l10 8 10-8" /></svg>
          <span>marla@dovecoteprops.com</span>
        </li>
        <li>
          <svg viewBox="0 0 24 24"><path d="M12 2a10 10 0 1 0 0 20 10 10 0 0 0 0-20zm-1 17.9A8 8 0 0 1 4.1 13H8c.1 2.5.9 4.9 3 6.9zM8 11H4.1A8 8 0 0 1 11 4.1C8.9 6.1 8.1 8.5 8 11zm2 0c.1-2.300.8-4.4 2-6 1.2 1.6 1.9 3.7 2 6zm0 2h4c-.1 2.3-.8 4.4-2 6-1.2-1.6-1.9-3.7-2-6zm3 6.9c2.1-2 2.9-4.4 3-6.9h3.9a8 8 0 0 1-6.9 6.9zM16 11c-.1-2.5-.9-4.9-3-6.9a8 8 0 0 1 6.9 6.9z"/></svg>
          <span>www.dovecoteprops.com</span>
        </li>
      </ul>
    </div>
  </section>

</body>
</html>
```